Simple and Clean business card design

We would like the design to be simple clean and to incorporate our colors.

We are open to your design and talent, we have the dots in our logo as we think of it as data points and we connect data points for people.

We are open to see the great creative and clean design you bring to the table

Contact Information for Business Card

please include: name, position, email, phone and website

Font styles to use
Sans Serif

Requirements
Must have
• my colors incorporated, simplicity
Nice to have
• lots of white space, simplicity
Should not have
• complexicity/ complex art

```html
<!DOCTYPE html>
<html lang="en">
<head>
<meta charset="utf-8">
<title>Sprigly Business Card</title>
<link rel="stylesheet" href="https://fonts.googleapis.com/css2?family=Work+Sans:wght@400;500;600&display=swap">
<style>
  :root {
    --page: #ebe6de;
    --card-dark: #000000;
    --card-light: #ffffff;
    --brand-blue: #5b7fc7;
    --brand-yellow: #f2b51b;
    --brand-green: #2fa44f;
    --text-light: #ffffff;
    --text-dark: #111111;
  }
  * { margin: 0; padding: 0; box-sizing: border-box; }
  html, body {
    width: 1200px;
    height: 900px;
    overflow: hidden;
    background: var(--page);
    font-family: "Work Sans", Arial, sans-serif;
  }
  .card {
    position: absolute;
    left: 261px;
    width: 656px;
    height: 357px;
    border-radius: 22px;
    overflow: hidden;
    background: var(--card-dark);
    box-shadow: 0 4px 10px rgba(0,0,0,0.25);
  }
  .card--front { top: 69px; }
  .card--back { top: 472px; }

  .front-shape {
    position: absolute;
    inset: 0;
    width: 656px;
    height: 357px;
  }

  .contact {
    position: absolute;
    left: 39px;
    top: 78px;
    color: var(--text-light);
  }
  .contact__name {
    font-size: 24px;
    font-weight: 500;
    letter-spacing: 1.2px;
    color: var(--brand-blue);
    line-height: 1;
    text-transform: uppercase;
  }
  .contact__role {
    font-size: 16px;
    line-height: 1;
    margin-top: 6px;
    letter-spacing: 0.4px;
  }
  .contact__address {
    margin-top: 28px;
    font-size: 16px;
    line-height: 21px;
    letter-spacing: 0.5px;
    font-style: normal;
  }
  .contact__list {
    list-style: none;
    margin-top: 20px;
    font-size: 16px;
    line-height: 21.5px;
    letter-spacing: 0.5px;
  }
  .contact__list li {
    display: flex;
    align-items: center;
    gap: 5px;
  }
  .contact__icon {
    width: 11px;
    height: 11px;
    flex: none;
  }

  .wordmark {
    position: absolute;
    display: flex;
    align-items: center;
    font-weight: 600;
    line-height: 1;
    letter-spacing: -1px;
  }
  .wordmark__dot {
    border-radius: 50%;
    background: var(--brand-green);
    flex: none;
  }
  .wordmark--front {
    left: 352px;
    top: 140px;
    font-size: 74px;
    color: var(--text-dark);
    gap: 12px;
  }
  .wordmark--front .wordmark__dot { width: 20px; height: 20px; }
  .wordmark--back {
    left: 150px;
    top: 128px;
    font-size: 100px;
    color: var(--text-light);
    gap: 16px;
  }
  .wordmark--back .wordmark__dot { width: 28px; height: 28px; }
</style>
</head>
<body>

<section class="card card--front" aria-label="Business card front">
  <svg class="front-shape" viewBox="0 0 656 357" aria-hidden="true">
    <path d="M455,6 A173.3,173.3 0 0 0 455,351 L471,357 L471,0 Z" fill="var(--brand-yellow)"/>
    <path d="M471,0 H656 V357 H471 A179,179 0 0 1 471,0 Z" fill="var(--card-light)"/>
  </svg>

  <div class="contact">
    <h1 class="contact__name">Daniel Reyes</h1>
    <p class="contact__role">Founder</p>
    <address class="contact__address">418 Cedarbrook Lane<br>Marlow, TX 78112</address>
    <ul class="contact__list">
      <li>
        <svg class="contact__icon" viewBox="0 0 12 12" aria-hidden="true"><path d="M3 1 L5 3.5 L4 5 Q5.5 7.5 7.5 8.5 L9 7.5 L11 9.5 L9.5 11 Q4 10 1.5 3 Z" fill="var(--brand-blue)"/></svg>
        0412 358 920
      </li>
      <li>
        <svg class="contact__icon" viewBox="0 0 12 12" aria-hidden="true"><rect x="1" y="2.5" width="10" height="7" fill="none" stroke="var(--brand-blue)" stroke-width="1.2"/><path d="M1 2.5 L6 6.5 L11 2.5" fill="none" stroke="var(--brand-blue)" stroke-width="1.2"/></svg>
        hello@northgridlabs.com
      </li>
      <li>
        <svg class="contact__icon" viewBox="0 0 12 12" aria-hidden="true"><g fill="none" stroke="var(--brand-blue)" stroke-width="1"><circle cx="6" cy="6" r="5"/><ellipse cx="6" cy="6" rx="2.2" ry="5"/><path d="M1 6 H11 M2 3.5 H10 M2 8.5 H10"/></g></svg>
        www.northgridlabs.com
      </li>
    </ul>
  </div>

  <div class="wordmark wordmark--front">
    <span class="wordmark__dot" aria-hidden="true"></span>
    <span class="wordmark__name">Sprigly</span>
  </div>
</section>

<section class="card card--back" aria-label="Business card back">
  <div class="wordmark wordmark--back">
    <span class="wordmark__dot" aria-hidden="true"></span>
    <span class="wordmark__name">Sprigly</span>
  </div>
</section>

</body>
</html>
```